Computer consultant business card

Bexil Software is a newly started computer consulting company. It's a small one-man company that provides mostly Vornix applications but also websites in collaboration with designers. I'm running this company on the side of full time university studies.

I want the final design to be clean and memorable. Be creative! :)

Some inspiration:
http://www.pixelmarta.com/design/48317
http://www.pixelmarta.com/design/2739164/business-card-design-by-frostlynk
http://www.pixelmarta.com/design/604281/business-card-design-by-koralind-vestrabanu

See attachment for my company logo.
Updates

I would like to thank everyone for submitting! I'll need a couple of days to review and ultimately select a design.

Target Market(s)

Non-technical entrepreneurs and small companies.

Industry/Entity Type

University

Requirements
Must have
• My company logo.
In any way, both colors from my logo.
First- and last name, e-mail and phone number.
Double-sided design.
Nice to have
• Something creative with the symbol in my logo

```html
<!DOCTYPE html>
<html lang="en">
<head>
<meta charset="utf-8">
<title>Bexil Software – Business Card</title>
<link rel="stylesheet" href="https://fonts.googleapis.com/css2?family=Saira:wght@400;500;600;700&display=swap">
<style>
  :root {
    --page: #e9e9eb;
    --card-white: #ffffff;
    --brand-blue: #2479f2;
    --brand-blue-soft: #4b91f5;
    --brand-blue-pattern: #3a88f5;
    --brand-dark: #333134;
    --text-light: #ffffff;
  }
  * { box-sizing: border-box; margin: 0; padding: 0; }
  html, body {
    width: 1200px;
    height: 820px;
    overflow: hidden;
    background: var(--page);
    font-family: "Saira", sans-serif;
  }
  .canvas {
    position: relative;
    width: 1200px;
    height: 820px;
  }
  .card {
    position: absolute;
    width: 540px;
    height: 310px;
    overflow: hidden;
    box-shadow: 0 6px 18px rgba(0,0,0,0.18);
  }

  /* Front side */
  .card-front {
    left: 50px;
    top: 140px;
    background: var(--card-white);
  }
  .front-logo {
    position: absolute;
    left: 70px;
    top: 46px;
    display: flex;
    align-items: center;
    gap: 22px;
  }
  .logo-dot {
    width: 78px;
    height: 78px;
    border-radius: 50%;
    background: var(--brand-blue);
  }
  .logo-name {
    font-weight: 600;
    font-size: 84px;
    line-height: 1;
    color: var(--brand-dark);
    letter-spacing: 1px;
  }
  .front-band {
    position: absolute;
    left: 0;
    bottom: 0;
    width: 100%;
    height: 138px;
    background: var(--brand-blue);
    color: var(--text-light);
    padding: 22px 0 0 28px;
  }
  .band-accent {
    position: absolute;
    right: 34px;
    top: 16px;
    width: 96px;
    height: 96px;
    border-radius: 50%;
    background: var(--brand-blue-soft);
  }
  .person-name {
    position: relative;
    font-size: 19px;
    font-weight: 400;
    line-height: 1.2;
    margin-bottom: 10px;
  }
  .person-name .first { font-weight: 700; }
  .contact-line {
    position: relative;
    display: flex;
    align-items: center;
    gap: 8px;
    font-size: 13.5px;
    letter-spacing: 0.8px;
    line-height: 1.75;
  }
  .contact-line svg { width: 12px; height: 12px; flex: none; }
  .contact-address { letter-spacing: 1.2px; }

  /* Back side */
  .card-back {
    left: 610px;
    top: 370px;
    background: var(--brand-blue);
  }
  .back-pattern {
    position: absolute;
    inset: 0;
    background: linear-gradient(135deg, var(--brand-blue) 0%, var(--brand-blue-pattern) 50%, var(--brand-blue) 100%);
  }
  .back-name {
    position: absolute;
    inset: 0;
    display: flex;
    align-items: center;
    justify-content: center;
    font-weight: 600;
    font-size: 120px;
    line-height: 1;
    color: var(--text-light);
    letter-spacing: 2px;
  }
</style>
</head>
<body>
<main class="canvas">

  <section class="card card-front" aria-label="Business card front">
    <div class="front-logo">
      <span class="logo-dot"></span>
      <span class="logo-name">bexil</span>
    </div>
    <div class="front-band">
      <span class="band-accent" aria-hidden="true"></span>
      <p class="person-name"><span class="first">First Name,</span> Last Name</p>
      <p class="contact-line">
        <svg viewBox="0 0 12 12" aria-hidden="true"><circle cx="6" cy="6" r="5.3" fill="none" stroke="#fff" stroke-width="1.2"/><path d="M4 3.3 L5.2 3.3 L5.5 4.8 L4.8 5.3 Q5.6 6.8 6.9 7.3 L7.4 6.6 L8.8 6.9 L8.8 8.1 Q5.2 8.6 3.8 4.2 Z" fill="#fff"/></svg>
        0412 386905
      </p>
      <p class="contact-line">
        <svg viewBox="0 0 12 12" aria-hidden="true"><rect x="1" y="3" width="10" height="7" rx="1" fill="#fff"/><path d="M1.5 3.5 L6 7 L10.5 3.5" fill="none" stroke="#2479f2" stroke-width="1"/></svg>
        info@bexil.com
      </p>
      <p class="contact-line contact-address">18, Larkwood Court, Tarlen, State 3147</p>
    </div>
  </section>

  <section class="card card-back" aria-label="Business card back">
    <div class="back-pattern" role="img" aria-label="Repeating pattern of faint brand symbols covering the blue back"></div>
    <div class="back-name">bexil</div>
  </section>

</main>
</body>
</html>
```